Bramwell IT Services Business Card

Bramwell IT Services are a Perth based IT Services company. We would like to incorporate our company logo (attached) and stick with the blue that is in that design. I would like a clean look design that isn't too busy, yet creates a lasting image that is instantly recognisable in the recipients mind.

Target Market(s)

The target audience is small/medium business owners.

Industry/Entity Type

Business

Font styles to use
Serif
Sans Serif

Colors

Designer to choose colors to be used in the design.

Requirements
Must have
• The design should include:
Business name: Bramwell IT Services
Directors Name: Marcus Tenley
Phone Number: 0483 562 904
Email: support@bramwellit.com.au
Website: www.bramwellit.com.au

```html
<!DOCTYPE html>
<html lang="en">
<head>
<meta charset="utf-8">
<title>Bramwell IT Services – Business Card</title>
<link rel="stylesheet" href="https://fonts.googleapis.com/css2?family=Questrial&family=Mulish:wght@700&display=swap">
<style>
  :root {
    --brand-blue: #1e8fe0;
    --card-black: #0b0b0c;
    --card-white: #f2f2f2;
    --text-light: #e6e6e6;
    --backdrop: #d9d6d2;
  }
  * { margin: 0; padding: 0; box-sizing: border-box; }
  html, body { width: 1200px; height: 900px; overflow: hidden; }
  body {
    background: var(--backdrop);
    font-family: "Questrial", sans-serif;
    position: relative;
  }
  .card {
    position: absolute;
    left: 290px;
    width: 620px;
    height: 354px;
    overflow: hidden;
    background: var(--card-black);
    box-shadow: 0 10px 28px rgba(0,0,0,0.25);
  }
  .card--back { top: 66px; }
  .card--front { top: 480px; }

  .wordmark {
    display: flex;
    align-items: center;
    gap: 10px;
    color: var(--brand-blue);
    font-family: "Questrial", sans-serif;
    font-size: 26px;
    letter-spacing: 1px;
    text-transform: uppercase;
    white-space: nowrap;
  }
  .wordmark__mark {
    flex: none;
    width: 16px; height: 16px;
    background: var(--brand-blue);
  }
  .card--back .wordmark {
    position: absolute;
    top: 50%; left: 50%;
    transform: translate(-50%, -50%);
  }

  .front__panel {
    position: absolute;
    top: 0; left: 0;
    width: 290px; height: 100%;
    background: var(--card-white);
    display: flex;
    align-items: center;
    justify-content: center;
    padding-bottom: 60px;
  }
  .front__panel .wordmark {
    font-size: 15px;
    letter-spacing: 0.8px;
    gap: 7px;
  }
  .front__panel .wordmark__mark { width: 10px; height: 10px; }

  .name-band {
    position: absolute;
    top: 104px; left: 290px; right: 0;
    height: 40px;
    background: var(--brand-blue);
    display: flex;
    align-items: center;
    padding-left: 30px;
  }
  .name-band::before {
    content: "";
    position: absolute;
    left: 0; top: -12px;
    width: 90px; height: 12px;
    background: var(--brand-blue);
    border-top-left-radius: 8px;
    border-top-right-radius: 8px;
  }
  .name-band__name {
    font-family: "Mulish", sans-serif;
    font-weight: 700;
    color: #fff;
    font-size: 19px;
    letter-spacing: 0.5px;
  }

  .contact {
    position: absolute;
    top: 178px; left: 314px;
    list-style: none;
    color: var(--text-light);
    font-size: 14px;
    line-height: 25px;
    letter-spacing: 0.6px;
  }
  .contact__label {
    display: inline-block;
    width: 22px;
    color: var(--brand-blue);
    font-weight: 700;
  }
</style>
</head>
<body>
  <section class="card card--back" aria-label="Business card back">
    <div class="wordmark"><span class="wordmark__mark"></span>Bramwell IT Services</div>
  </section>

  <section class="card card--front" aria-label="Business card front">
    <div class="front__panel">
      <div class="wordmark"><span class="wordmark__mark"></span>Bramwell IT Services</div>
    </div>
    <div class="name-band"><span class="name-band__name">Marcus Tenley</span></div>
    <ul class="contact">
      <li><span class="contact__label">P</span>0483 562 904</li>
      <li><span class="contact__label">E</span>support@bramwellit.com.au</li>
      <li><span class="contact__label">W</span>www.bramwellit.com.au</li>
    </ul>
  </section>
</body>
</html>
```